VELMOR Website Design

We need a website designed for our company VELMOR. We are a luxury lifestyle club that will provide benefits and services for our members. The site should be clean & sleek, preferably using black and white (or darker colors). (example sites: stravenhall.example, plinth.example)

Here is a link of a sample page I did using wix. (https://dunmere7.sitehostly.example/mysite) This can be used to get a general idea.

Target Market(s)

Upper Middle Class in the United States

Number of Pages Required

5+ page

Font styles to use
Sans Serif
Other font styles liked:
• Arial (or other similar fonts)

Requirements
Must have
• A clean design that is eye-catching and speaks to our company.
Nice to have
• Ideas for copy.

```html
<!DOCTYPE html>
<html lang="en">
<head>
<meta charset="utf-8">
<title>VELMOR — Contact</title>
<link href="https://fonts.googleapis.com/css2?family=Montserrat:wght@400;500;600;700&display=swap" rel="stylesheet">
<style>
:root{
  --ink:#ffffff;
  --dark:#242424;
  --panel:#1b1b1b;
  --blue:#1463e6;
  --muted:#8a8a8a;
  --line:#6c6c6c;
  --map:#e9e9e9;
}
*{margin:0;padding:0;box-sizing:border-box}
html,body{width:1200px;height:1158px;overflow:hidden;background:var(--dark)}
body{font-family:"Montserrat",Arial,sans-serif;color:var(--ink);position:relative}
.abs{position:absolute}

.hero{left:0;top:0;width:1200px;height:236px;background:linear-gradient(180deg,#1f2430 0%,#4a4740 45%,#3a4a55 80%,#2c3a44 100%)}
.hero-photo{position:absolute;inset:0;background:radial-gradient(ellipse at 50% 55%,rgba(150,130,90,.35),rgba(0,0,0,0) 60%)}
.logo{left:113px;top:18px;width:194px;height:51px;border:2px solid var(--ink);font-size:40px;font-weight:500;letter-spacing:1px;display:flex;align-items:center;justify-content:center;line-height:1}
.nav{top:36px;left:714px;font-size:13px;font-weight:500}
.nav a{color:var(--ink);text-decoration:none;position:absolute;white-space:nowrap}
.nav a.current{color:var(--blue);padding-bottom:4px;border-bottom:2px solid var(--blue)}
.search{left:1059px;top:36px;width:20px;height:20px;border-radius:50%;background:var(--blue)}
.page-title{left:112px;top:124px;font-size:30px;font-weight:600;letter-spacing:.5px}

.office{left:0;top:236px;width:1200px;height:276px;background:var(--dark)}
.heading{font-size:14.5px;font-weight:600;letter-spacing:.1px;white-space:nowrap}
.rule{height:2px;width:56px;background:var(--line);margin-top:8px}
.icon{width:36px;height:36px;border-radius:50%;background:var(--blue);display:flex;align-items:center;justify-content:center}
.info{font-size:10.5px;font-weight:600;line-height:1.45;white-space:nowrap}
.intro{left:446px;top:318px;width:640px;font-size:9.9px;letter-spacing:-0.05px;line-height:20px;font-weight:500}

.map{left:0;top:512px;width:1200px;height:381px;background:linear-gradient(135deg,#efefef,#e2e2e2 50%,#ececec)}
.pin{left:558px;top:672px;width:92px;height:32px;background:var(--blue);font-size:13px;font-weight:500;display:flex;align-items:center;justify-content:center}
.pin::after{content:"";position:absolute;left:0;bottom:-8px;border-left:8px solid var(--blue);border-bottom:8px solid transparent}

.form{left:779px;top:574px;width:308px;height:320px;background:var(--panel)}
.field{position:absolute;left:17px;width:274px;border:1px solid #4a4a4a;background:#1d1d1d;font-size:10.5px;font-weight:500;padding:9px 10px}
.send{left:779px;top:894px;width:308px;height:39px;background:var(--blue);font-size:15px;font-weight:500;padding-left:16px;display:flex;align-items:center}

.foot-head{font-size:11.5px;font-weight:600;color:var(--blue)}
.foot-text{font-size:10.5px;font-weight:600;line-height:1.3}
.social{width:29px;height:29px;border-radius:50%;border:1px solid #777}
.subscribe{left:778px;top:1062px;width:144px;height:26px;border:1px solid #777;border-radius:14px;font-size:10.5px;color:var(--muted);padding:6px 13px}
.bottom-bar{left:0;top:1113px;width:1200px;height:45px;border-top:1px solid #333;background:var(--dark)}
</style>
</head>
<body>

<header class="abs hero" role="img" aria-label="Evening photograph of a grand illuminated hotel facade">
  <div class="hero-photo"></div>
</header>
<div class="abs logo">VELMOR</div>
<nav class="abs nav">
  <a style="left:0;top:0">Home</a>
  <a style="left:59px;top:0">About us</a>
  <a style="left:136px;top:0">Services &amp; Benefits</a>
  <a class="current" style="left:277px;top:0">Contact</a>
</nav>
<div class="abs search">
  <svg width="20" height="20" viewBox="0 0 20 20"><circle cx="9" cy="9" r="3.5" fill="none" stroke="#fff" stroke-width="1.8"/><line x1="11.6" y1="11.6" x2="14" y2="14" stroke="#fff" stroke-width="1.8" stroke-linecap="round"/></svg>
</div>
<h1 class="abs page-title">CONTACT</h1>

<section class="abs office"></section>
<div class="abs" style="left:113px;top:272px">
  <h2 class="heading">OUR HEADDING OFFICE</h2><div class="rule"></div>
</div>
<div class="abs" style="left:446px;top:272px">
  <h2 class="heading">WE’D LOVE TO HEAR FROM YOU</h2><div class="rule"></div>
</div>

<div class="abs icon" style="left:112px;top:323px">
  <svg width="16" height="16" viewBox="0 0 16 16"><path d="M8 2 1.5 8H4v6h3V10h2v4h3V8h2.5z" fill="#fff"/></svg>
</div>
<p class="abs info" style="left:164px;top:324px;line-height:1.2">Harrowgate Row LLC 2300 Linden,<br>Suite 245 Ashford, IL 60999</p>

<div class="abs icon" style="left:112px;top:380px">
  <svg width="16" height="16" viewBox="0 0 16 16"><circle cx="8" cy="8" r="6.5" fill="none" stroke="#fff" stroke-width="1.6"/><path d="M1.5 8h13M8 1.5c2.2 2 2.2 11 0 13M8 1.5c-2.2 2-2.2 11 0 13" stroke="#fff" stroke-width="1.2" fill="none"/></svg>
</div>
<p class="abs info" style="left:164px;top:380px;line-height:1.9">WEBSITE &amp; ONLINE STORE<br>http://www.velmor.example</p>

<div class="abs icon" style="left:112px;top:437px">
  <svg width="16" height="16" viewBox="0 0 16 16"><path d="M4 2h3l1 3-2 1.3a8 8 0 0 0 3.7 3.7L11 8l3 1v3a2 2 0 0 1-2 2A10 10 0 0 1 2 4a2 2 0 0 1 2-2z" fill="#fff"/></svg>
</div>
<p class="abs info" style="left:164px;top:437px;line-height:1.6">TELEPHONE<br>(000) 555 010201 &nbsp;- (000) 555 010202</p>

<p class="abs intro">Lorem Ipsum is simply dummy text of the printing and typesetting industry. Lorem Ipsum has been the industry's standard dummy text ever since the 1500s, when an unknown printer took a galley of type and scrambled it to make a type specimen book. It has survived not only five centuries, but also the leap into electronic typesetting, remaining essentially unchanged. It was popularised in the 1960s with the release of Typeloft sheets containing Lorem Ipsum passages, and more recently with desktop publishing software like Quillset Layout including versions of Lorem Ipsum.</p>

<div class="abs map" role="img" aria-label="Light grey street map of the city area around the office"></div>
<div class="abs pin">VELMOR</div>

<form class="abs form">
  <h2 class="heading" style="position:absolute;left:15px;top:18px">CONTACT FORM</h2>
  <div class="rule" style="position:absolute;left:17px;top:42px;width:64px;margin:0"></div>
  <div class="field" style="top:68px;height:28px;padding-top:8px">Your name</div>
  <div class="field" style="top:119px;height:28px;padding-top:8px">Your email</div>
  <div class="field" style="top:166px;height:130px">Your message</div>
</form>
<div class="abs send">SEND MESSAGE</div>

<p class="abs foot-text" style="left:111px;top:983px;line-height:1.9">Copyright 2017-18 <span style="color:var(--blue)">VELMOR</span></p>
<div class="abs social" style="left:112px;top:1038px" aria-label="Social link"></div>
<div class="abs social" style="left:149px;top:1038px" aria-label="Social link"></div>
<div class="abs social" style="left:186px;top:1038px" aria-label="Social link"></div>
<div class="abs social" style="left:223px;top:1038px" aria-label="Social link"></div>

<h3 class="abs foot-head" style="left:444px;top:982px">Our location</h3>
<div class="abs foot-text" style="left:444px;top:1011px">
  <p>Harrowgate Row LLC 1234 Linden,<br>Suite 123 Ashford, IL 00000</p>
  <p style="margin-top:7px">Phone : +00 1 55501020</p>
  <p style="margin-top:7px">Email : info@velmor.example</p>
</div>

<h3 class="abs foot-head" style="left:778px;top:982px">Keep in touch</h3>
<p class="abs foot-text" style="left:779px;top:1003px;line-height:20px;width:300px">Lorem ipsum dolor sit amet, consectetur adi sollicitud ante tellus ornare mi, et mollis</p>
<div class="abs subscribe">Your email
  <svg style="position:absolute;right:9px;top:7px" width="12" height="11" viewBox="0 0 12 11"><path d="M1 5.5h9M6 1.5l4 4-4 4" stroke="#9a9a9a" stroke-width="1.8" fill="none"/></svg>
</div>

<div class="abs bottom-bar">
  <svg style="position:absolute;left:590px;top:15px" width="20" height="13" viewBox="0 0 20 13"><path d="M2 11 10 3l8 8" stroke="#fff" stroke-width="2.6" fill="none"/></svg>
</div>

</body>
</html>
```